Norvane Stationery Design Project

We need stationary design that goes with the attached logo. We have logo in two different versions. One in Red/Black and the other in Blue/Green. Red/Black is going to be our primary color and we are planning to use Blue/Green occasionally as necessary.

So we need stationary design in both color combinations. Maybe you can work with Red/Black first and once we decide on the design, then you can show the Blue/Green variation.

Please see the attached png and psd files for logo.

Target Market(s)

IT departments of Medium size Enterprises.

Industry/Entity Type

Work

Requirements
Must have
• -Letter head
-Cover page design for white papers and articles that are going to publish
-Business Card
-Envelope design
Nice to have
• - High level design template that we can follow for our internal web applications

```html
<!DOCTYPE html>
<html lang="en">
<head>
<meta charset="utf-8">
<title>Norvane Software – Business Card</title>
<link rel="stylesheet" href="https://fonts.googleapis.com/css2?family=Lato:wght@400;700;900&display=swap">
<style>
  :root {
    --backdrop: #2b2b2d;
    --brand-red: #d8121a;
    --brand-red-deep: #a90d13;
    --ink: #1a1a1a;
    --paper: #ffffff;
    --paper-shade: #ececec;
    --soft-white: rgba(255, 255, 255, 0.88);
  }
  * { box-sizing: border-box; margin: 0; padding: 0; }
  html, body { width: 1200px; height: 997px; overflow: hidden; }
  body {
    background: var(--backdrop);
    font-family: "Lato", Arial, sans-serif;
    position: relative;
  }
  .card {
    position: absolute;
    width: 520px;
    height: 297px;
    overflow: hidden;
    box-shadow: 0 14px 30px rgba(0, 0, 0, 0.55);
  }

  /* Front side */
  .card-front {
    left: 110px;
    top: 95px;
    background: linear-gradient(160deg, var(--brand-red) 0%, var(--brand-red-deep) 100%);
    color: var(--paper);
  }
  .card-front .brand {
    position: absolute;
    left: 70px;
    top: 100px;
  }
  .card-front .slogan {
    position: absolute;
    left: 70px;
    bottom: 52px;
    font-size: 12px;
    letter-spacing: 3px;
    color: var(--soft-white);
    text-transform: uppercase;
  }

  /* Shared brand lockup */
  .brand {
    display: flex;
    align-items: center;
    gap: 14px;
  }
  .brand-square {
    width: 34px;
    height: 34px;
    background: currentColor;
  }
  .brand-name {
    font-weight: 900;
    font-size: 30px;
    letter-spacing: 5px;
    text-transform: uppercase;
    line-height: 1;
  }

  /* Back side */
  .card-back {
    left: 570px;
    top: 520px;
    background: linear-gradient(160deg, var(--brand-red) 0%, var(--brand-red-deep) 100%);
    color: var(--paper);
  }
  .card-back .upper {
    position: absolute;
    left: 0; top: 0;
    width: 100%;
    height: 150px;
    background: linear-gradient(180deg, var(--paper) 0%, var(--paper-shade) 100%);
  }
  .card-back .brand {
    position: absolute;
    left: 110px;
    top: 42px;
    color: var(--ink);
  }
  .card-back .brand .brand-square { background: var(--brand-red); }
  .card-back .holder-name {
    position: absolute;
    left: 34px;
    bottom: 16px;
    font-weight: 900;
    font-size: 17px;
    letter-spacing: 1px;
    color: var(--ink);
  }
  .card-back .pointer {
    position: absolute;
    left: 72px;
    top: 149px;
  }
  .contact-list {
    position: absolute;
    left: 34px;
    top: 176px;
    list-style: none;
  }
  .contact-list li {
    display: flex;
    align-items: center;
    gap: 12px;
    font-weight: 700;
    font-size: 17px;
    height: 33px;
  }
  .contact-list svg { width: 18px; height: 18px; flex: none; }
  .company-info {
    position: absolute;
    right: 28px;
    top: 178px;
    text-align: left;
    font-weight: 700;
  }
  .company-info .website {
    font-size: 15px;
    padding-bottom: 8px;
    border-bottom: 2px solid var(--soft-white);
  }
  .company-info .address {
    font-size: 12px;
    padding-top: 8px;
    color: var(--soft-white);
  }
</style>
</head>
<body>
  <section class="card card-front" aria-label="Business card front">
    <div class="brand">
      <span class="brand-square"></span>
      <span class="brand-name">Norvane Software</span>
    </div>
    <p class="slogan">Your slogan / tagline here</p>
  </section>

  <section class="card card-back" aria-label="Business card back">
    <div class="upper">
      <div class="brand">
        <span class="brand-square"></span>
        <span class="brand-name">Norvane Software</span>
      </div>
      <p class="holder-name">YOUR NAME</p>
    </div>
    <svg class="pointer" width="24" height="12" viewBox="0 0 24 12" aria-hidden="true">
      <polygon points="0,0 24,0 12,12" fill="#ececec"/>
    </svg>
    <ul class="contact-list">
      <li>
        <svg viewBox="0 0 18 18" aria-hidden="true"><rect x="4.5" y="1" width="9" height="16" rx="1.5" fill="none" stroke="#fff" stroke-width="1.6"/><line x1="7.5" y1="14" x2="10.5" y2="14" stroke="#fff" stroke-width="1.4"/></svg>
        (555) 014-2230
      </li>
      <li>
        <svg viewBox="0 0 18 18" aria-hidden="true"><path d="M2 7 Q9 1 16 7 L14 9 L12 7.5 L12 6 Q9 5 6 6 L6 7.5 L4 9 Z" fill="#fff"/><rect x="4" y="10" width="10" height="6" rx="1" fill="#fff"/></svg>
        (555) 017-6481
      </li>
      <li>
        <svg viewBox="0 0 18 18" aria-hidden="true"><rect x="1.5" y="4" width="15" height="10" fill="none" stroke="#fff" stroke-width="1.6"/><polyline points="1.5,4 9,10 16.5,4" fill="none" stroke="#fff" stroke-width="1.6"/></svg>
        info@norvanesoftware.com
      </li>
    </ul>
    <div class="company-info">
      <p class="website">www.norvanesoftware.com</p>
      <p class="address">P.O. Box 81, Marlow AL, 36599</p>
    </div>
  </section>
</body>
</html>
```